Change of trading name, rebrand

existing website to be updated with new theme and logo. existing website is
www.harlowbrentmere.com.au
Industry/Entity Type
Construction
Coding
Coded - Design and coding required
Number of Pages Required
5+ page
Requirements
Must have
- be mobile phone friendly

```html
<!DOCTYPE html>
<html lang="en">
<head>
<meta charset="utf-8">
<title>HBR Plant Hire</title>
<link href="https://fonts.googleapis.com/css2?family=Montserrat:wght@400;500;600;700;800&display=swap" rel="stylesheet">
<style>
:root{
  --navy:#25247c;
  --navy-dark:#1d1c66;
  --ink:#111;
  --text:#3a3a3a;
  --lavender:#ececf8;
  --white:#fff;
  --card-shadow:0 4px 14px rgba(0,0,0,.14);
}
*{margin:0;padding:0;box-sizing:border-box}
html,body{width:1200px;height:3980px;overflow:hidden}
body{position:relative;font-family:"Montserrat",sans-serif;color:var(--ink);background:var(--white)}
.abs{position:absolute}
a{color:inherit;text-decoration:none}
.btn{position:absolute;display:flex;align-items:center;justify-content:center;background:var(--navy);color:#fff;font-weight:600;font-size:16px;letter-spacing:.3px}
.brand{font-weight:800;color:var(--navy);line-height:1;letter-spacing:1px}

/* header */
.topbar{left:556px;top:0;width:644px;height:43px;background:var(--navy);clip-path:polygon(16px 0,100% 0,100% 100%,0 100%)}
.topbar span{position:absolute;top:12px;color:#fff;font-size:14px;display:flex;align-items:center;gap:8px}
.logo{left:108px;top:34px;font-size:40px}
.logo small{display:block;font-size:13px;letter-spacing:5px;margin-top:6px;color:var(--ink);font-weight:700}
.nav{left:307px;top:82px;display:flex;gap:31px;font-size:13.5px;font-weight:500;color:#222}
.nav .active{color:var(--navy);border-bottom:2px solid var(--navy);padding-bottom:3px}

/* hero */
.hero{left:0;top:131px;width:1200px;height:570px;background:linear-gradient(120deg,#2b2a3c 0%,#5a4636 30%,#c77a3a 55%,#e59a45 70%,#3a3a4a 100%)}
.hero h1{position:absolute;left:110px;top:110px;color:#fff;font-size:58px;font-weight:700;line-height:64px;letter-spacing:2px}
.hero p{position:absolute;left:110px;top:258px;color:#fff;font-size:23px;line-height:31px;width:460px}
.hero .outline{position:absolute;left:110px;top:345px;width:178px;height:48px;border:3px solid #fff;color:#fff;display:flex;align-items:center;justify-content:center;font-weight:600;font-size:15px}
.wave{left:0;top:630px}

/* about */
.about-mark{left:88px;top:880px;width:500px;text-align:center;font-size:120px}
.about-mark small{display:block;font-size:34px;letter-spacing:12px;color:var(--ink);margin-top:14px}
.about h2{position:absolute;left:624px;top:776px;font-size:37px;font-weight:800}
.about p{position:absolute;left:624px;top:848px;width:435px;font-size:15.5px;line-height:30px;color:var(--text)}

/* partners */
.partners-title{left:0;width:1200px;top:1256px;text-align:center;font-size:24px;font-weight:700}
.partner{top:1325px;width:182px;height:99px;background:#fff;border-radius:6px;box-shadow:var(--card-shadow);display:flex;align-items:center;justify-content:center}
.partner i{display:block;width:110px;height:34px;border-radius:4px;background:#d5d5dd}
.dots{left:552px;top:1473px;display:flex;gap:10px}
.dots i{width:26px;height:5px;border-radius:3px;background:#c9c8ec}
.dots i:first-child{background:var(--navy)}

/* stats */
.stats{left:0;top:1553px;width:1200px;height:301px;background:linear-gradient(135deg,#e6e6f7,#f2f2fb 50%,#e4e4f5)}
.stat{position:absolute;top:70px;width:190px;text-align:center;font-size:15px;font-weight:500;line-height:28px;color:#111}
.stat svg{display:block;margin:0 auto 6px}
.stat b{display:block;font-size:32px;font-weight:700;color:var(--navy);line-height:40px}

/* categories */
.arrow{width:54px;height:54px;border-radius:50%;display:flex;align-items:center;justify-content:center}
.tab{top:1940px;width:228px;height:132px;background:#fff;box-shadow:var(--card-shadow);border-radius:4px;display:flex;flex-direction:column;align-items:center;justify-content:center;gap:14px;font-weight:700;font-size:20px}
.tab.on{background:var(--navy);color:#fff}
.tab .ico{width:52px;height:34px;border-radius:6px;background:var(--navy)}
.tab.on .ico{background:#fff}
.cat h2{position:absolute;left:117px;top:2182px;font-size:30px;font-weight:800}
.cat p{position:absolute;left:117px;top:2240px;width:430px;font-size:15.5px;line-height:30px;color:var(--text)}
.cat-photo{left:595px;top:2163px;width:471px;height:433px;border-radius:6px;background:linear-gradient(160deg,#3a4560 0%,#c57a3c 45%,#e5a048 60%,#3c3024 100%);box-shadow:var(--card-shadow)}

/* contact */
.map{left:0;top:2704px;width:1200px;height:703px;background:linear-gradient(120deg,#e4eee0,#eef2ea 50%,#dfeadb)}
.form-card{left:108px;top:2800px;width:635px;height:515px;background:#fff}
.form-card h3{position:absolute;left:0;width:100%;top:40px;text-align:center;font-size:21px;font-weight:700}
.field{position:absolute;border:1.5px solid #555;border-radius:6px;font-size:13px;color:#555;padding:17px 16px}
.info-card{left:743px;top:2800px;width:343px;height:517px;background:var(--navy);border-radius:6px;color:#fff}
.info-card h3{position:absolute;left:34px;top:55px;font-size:28px;font-weight:700;line-height:38px}
.info-card hr{position:absolute;left:38px;top:153px;width:220px;border:0;border-top:1.5px solid #9b9bd3}
.info-row{position:absolute;left:40px;display:flex;gap:20px;font-size:22px;font-weight:700;line-height:32px}

/* cta + footer */
.cta{left:110px;top:3496px;font-size:29px;font-weight:700}
.rule{left:108px;width:978px;border-top:1.5px solid var(--navy)}
.f-logo{left:108px;top:3680px;font-size:56px}
.f-logo small{display:block;font-size:16px;letter-spacing:6px;color:var(--ink);margin-top:10px}
.f-head{top:3656px;font-size:24px;font-weight:700}
.f-list{top:3718px;list-style:none;font-size:14px;line-height:28.3px;color:#444}
.copy{left:0;width:1200px;top:3942px;text-align:center;font-size:13px;color:#333}
</style>
</head>
<body>

<header>
  <div class="abs topbar">
    <span style="left:58px">
      <svg width="22" height="22" viewBox="0 0 24 24"><circle cx="12" cy="12" r="10.5" fill="none" stroke="#fff" stroke-width="1.6"/><path d="M8.5 7c.6-.4 1.2 0 1.5.6l.8 1.6c.2.5 0 1-.4 1.3l-.6.5c.6 1.4 1.7 2.5 3.1 3.1l.5-.6c.3-.4.8-.6 1.3-.4l1.6.8c.6.3 1 .9.6 1.5-.7 1.2-2 1.6-3.2 1.1-2.6-1-4.7-3.1-5.7-5.7-.5-1.3-.1-2.6 1.1-3.2z" fill="#fff"/></svg>
      1300 555 014
    </span>
    <span style="left:262px">
      <svg width="30" height="30" viewBox="0 0 24 24"><circle cx="12" cy="12" r="11" fill="none" stroke="#fff" stroke-width="1.4"/><path d="M12 5.5a4.2 4.2 0 0 0-4.2 4.2c0 3 4.2 7.8 4.2 7.8s4.2-4.8 4.2-7.8A4.2 4.2 0 0 0 12 5.5z" fill="#fff"/><circle cx="12" cy="9.7" r="1.6" fill="var(--navy)"/></svg>
      18 Kessing Rd, Wyndale QLD 4290
    </span>
  </div>
  <div class="abs brand logo">HBR<small>PLANT HIRE</small></div>
  <nav class="abs nav">
    <a class="active">HOME</a><a>ABOUT US</a><a>PLANT HIRE</a><a>MAJOR PROJECT SNAPSHOT</a><a>POLICIES</a><a>JOBS</a><a>CONTACT US</a>
  </nav>
</header>

<section class="abs hero" role="img" aria-label="Excavator working on a site at sunset">
  <h1>HBR Heavy<br>Equipment Hire</h1>
  <p>Committed to superior quality plant hire services.</p>
  <a class="outline">GET STARTED</a>
</section>
<svg class="abs wave" width="1200" height="80" viewBox="0 0 1200 80">
  <path d="M0 55 L330 18 L1200 50 L1200 80 L0 80Z" fill="var(--navy)"/>
  <path d="M0 66 L330 32 L1200 60 L1200 80 L0 80Z" fill="#fff"/>
</svg>

<section class="about">
  <div class="abs brand about-mark">HBR<small>PLANT HIRE</small></div>
  <h2>ABOUT US</h2>
  <p>Harlow Brentmere Resources Pty Ltd trading as HBR Heavy Equipment is a privately owned company that was established in 2010. Our founder saw a need in the market for a plant and equipment supplier who was committed to the successful delivery of client’s projects. With this vision and focus HBR has successfully seen our clients deliver on-time and on-budget.</p>
  <a class="btn" style="left:626px;top:1128px;width:178px;height:47px">READ MORE</a>
</section>

<section>
  <h2 class="abs partners-title">OUR PARTNERS</h2>
  <div class="abs partner" style="left:106px"><i></i></div>
  <div class="abs partner" style="left:306px"><i></i></div>
  <div class="abs partner" style="left:503px"><i></i></div>
  <div class="abs partner" style="left:702px"><i></i></div>
  <div class="abs partner" style="left:896px"><i></i></div>
  <div class="abs dots"><i></i><i></i><i></i></div>
</section>

<section class="abs stats">
  <div class="stat" style="left:107px"><svg width="56" height="56" viewBox="0 0 56 56"><path d="M14 22a14 12 0 0 1 28 0z M10 22h36v4H10z" fill="var(--navy)"/><circle cx="28" cy="34" r="7" fill="var(--navy)"/><path d="M12 56c0-9 7-14 16-14s16 5 16 14z" fill="var(--navy)"/></svg><b>20+</b>YEARS OF<br>EXPERIENCE</div>
  <div class="stat" style="left:299px"><svg width="76" height="56" viewBox="0 0 76 56"><rect x="22" y="28" width="30" height="14" fill="var(--navy)"/><rect x="20" y="44" width="42" height="10" rx="5" fill="var(--navy)"/><path d="M40 28 L18 6 L6 30" fill="none" stroke="var(--navy)" stroke-width="5"/></svg><b>100+</b>MACHINES IN<br>FLEET</div>
  <div class="stat" style="left:498px;top:80px"><svg width="56" height="66" viewBox="0 0 56 66"><path d="M18 2 L26 22 L42 36 L50 60 L8 62 L6 30 Z" fill="var(--navy)"/></svg>ONE OF QLD’S<br>LARGEST<br>SUPPLIERS</div>
  <div class="stat" style="left:691px"><svg width="56" height="66" viewBox="0 0 24 28"><path d="M12 1a9 9 0 0 0-9 9c0 6.5 9 15 9 15s9-8.5 9-15a9 9 0 0 0-9-9z" fill="var(--navy)"/><circle cx="12" cy="10" r="4" fill="#fff"/><ellipse cx="12" cy="26" rx="7" ry="1.6" fill="var(--navy)"/></svg>ONSITE<br>SERVICING</div>
  <div class="stat" style="left:889px"><svg width="60" height="60" viewBox="0 0 24 24"><path d="M10.3 1h3.4l.5 3 2 .9 2.5-1.8 2.4 2.4-1.8 2.5.9 2 3 .5v3.4l-3 .5-.9 2 1.8 2.5-2.4 2.4-2.5-1.8-2 .9-.5 3h-3.4l-.5-3-2-.9-2.5 1.8-2.4-2.4 1.8-2.5-.9-2-3-.5v-3.4l3-.5.9-2-1.8-2.5 2.4-2.4 2.5 1.8 2-.9z" fill="var(--navy)"/><circle cx="12" cy="12" r="4.5" fill="#fff"/><circle cx="12" cy="12" r="2.5" fill="var(--navy)"/></svg>CUSTOM<br>MACHINE<br>ATTACHMENTS</div>
</section>

<section class="cat">
  <div class="abs arrow" style="left:22px;top:1977px;background:#7c7bdb"><svg width="20" height="20" viewBox="0 0 20 20"><path d="M13 3 L6 10 L13 17" fill="none" stroke="#fff" stroke-width="3"/></svg></div>
  <div class="abs arrow" style="left:1119px;top:1977px;background:var(--navy)"><svg width="20" height="20" viewBox="0 0 20 20"><path d="M7 3 L14 10 L7 17" fill="none" stroke="#fff" stroke-width="3"/></svg></div>
  <div class="abs tab on" style="left:110px"><span class="ico" role="img" aria-label="Excavator icon"></span>EXCAVATORS</div>
  <div class="abs tab" style="left:359px"><span class="ico" role="img" aria-label="Dozer icon"></span>DOZERS</div>
  <div class="abs tab" style="left:610px"><span class="ico" role="img" aria-label="Dump truck icon"></span>DUMP TRUCKS</div>
  <div class="abs tab" style="left:859px"><span class="ico" role="img" aria-label="Grader icon"></span>GRADERS</div>
  <h2>EXCAVATORS</h2>
  <p>HBR Heavy Equipment has one of the largest fleet of excavators for hire in South East Queensland, north to Sunshine Coast, south into Northern New South Wales and inland to the Surat Basin, Toowoomba and Dalby<br>We are proud of our broad range of excavators fitted with state-of-the-art GPS, spanning reliable and trusted brands such as Ridgeway excavators for hire,</p>
  <a class="btn" style="left:113px;top:2518px;width:178px;height:47px">READ MORE</a>
  <div class="abs cat-photo" role="img" aria-label="Orange excavator on a dirt site at sunset"></div>
</section>

<section>
  <div class="abs map" role="img" aria-label="Street map around the depot"></div>
  <form class="abs form-card">
    <h3>CONTACT US TODAY FOR A FREE QUOTE</h3>
    <div class="field" style="left:30px;top:93px;width:576px;height:50px">Name</div>
    <div class="field" style="left:30px;top:151px;width:282px;height:50px">Phone</div>
    <div class="field" style="left:324px;top:151px;width:282px;height:50px">Email</div>
    <div class="field" style="left:30px;top:211px;width:576px;height:50px">Address</div>
    <div class="field" style="left:30px;top:272px;width:576px;height:124px">Message</div>
    <a class="btn" style="left:230px;top:420px;width:178px;height:48px;font-size:15px">SUBMIT</a>
  </form>
  <div class="abs info-card">
    <h3>CONTACT<br>INFORMATION</h3>
    <hr>
    <div class="info-row" style="top:216px"><svg width="54" height="54" viewBox="0 0 24 24"><circle cx="12" cy="12" r="10.8" fill="none" stroke="#fff" stroke-width="1.3"/><path d="M8.5 7c.6-.4 1.2 0 1.5.6l.8 1.6c.2.5 0 1-.4 1.3l-.6.5c.6 1.4 1.7 2.5 3.1 3.1l.5-.6c.3-.4.8-.6 1.3-.4l1.6.8c.6.3 1 .9.6 1.5-.7 1.2-2 1.6-3.2 1.1-2.6-1-4.7-3.1-5.7-5.7-.5-1.3-.1-2.6 1.1-3.2z" fill="#fff"/></svg><span style="padding-top:10px">1300 555 014</span></div>
    <div class="info-row" style="top:296px"><svg width="54" height="54" viewBox="0 0 24 24"><circle cx="12" cy="12" r="10.8" fill="none" stroke="#fff" stroke-width="1.3"/><path d="M12 5.5a4.2 4.2 0 0 0-4.2 4.2c0 3 4.2 7.8 4.2 7.8s4.2-4.8 4.2-7.8A4.2 4.2 0 0 0 12 5.5z" fill="#fff"/><circle cx="12" cy="9.7" r="1.6" fill="var(--navy)"/></svg><span>18 Kessing Rd,<br>Wyndale<br>QLD 4290</span></div>
  </div>
</section>

<section>
  <h2 class="abs cta">CONTACT US TODAY FOR A FREE QUOTE</h2>
  <a class="btn" style="left:896px;top:3493px;width:178px;height:47px;font-size:15px">GET A QUOTE</a>
</section>

<footer>
  <div class="abs rule" style="top:3594px"></div>
  <div class="abs brand f-logo">HBR<small>PLANT HIRE</small></div>
  <h4 class="abs f-head" style="left:380px">Quick Links</h4>
  <h4 class="abs f-head" style="left:616px">Other Links</h4>
  <div class="abs rule" style="left:616px;width:413px;top:3694px"></div>
  <ul class="abs f-list" style="left:383px"><li>Home</li><li>About us</li><li>Machine Operator Jobs</li><li>Plant Hire</li><li>Attachments Hire</li><li>Policies</li></ul>
  <ul class="abs f-list" style="left:616px"><li>Articulated Dump Trucks</li><li>Hire</li><li>Dozer Hire</li><li>Excavator Diggers Hire</li><li>Grader Hire</li><li>Attachments Hire</li></ul>
  <ul class="abs f-list" style="left:891px"><li>Backhoe Hire</li><li>Compactors Hire</li><li>Loader Hire</li><li>Skid Steer Hire</li><li>Water Cart Hire</li></ul>
  <div class="abs rule" style="top:3920px"></div>
  <p class="abs copy">© 2024 HBR Plant Hire &nbsp;All rights reserved</p>
</footer>

</body>
</html>
```